Duct Manufacturing Company new to the industry needs business card and stationary design

we are sheet metal duct manufacturers looking for a business card design to fit my new business logo.
nothing to crazy that will date, but want it to stand out from the crowed.
I'm sure you guys will work it out.

Contact Information for Business Card

Glen Marsh
Director

Address
17 Dorwell St
Tarrowell NSW 2794

0438 760 514

Sales@flowbend.com.au

Font styles to use
Other font styles liked:
• BankGothic md bt

Requirements
Nice to have
• Like the idea of corner rounded to match logo
• like to keep colours flowing
• font I like sharp square not rounded

```html
<!DOCTYPE html>
<html lang="en">
<head>
<meta charset="utf-8">
<title>Flowbend Industries – Business Card</title>
<link rel="stylesheet" href="https://fonts.googleapis.com/css2?family=Michroma&display=swap">
<style>
  :root {
    --backdrop: #3a3532;
    --card: #161616;
    --card-edge: #232323;
    --green: #7cc242;
    --blue: #1e8fd9;
    --white: #f2f2f2;
    --divider: #4a4a4a;
    --icon-ink: #161616;
  }
  * { margin: 0; padding: 0; box-sizing: border-box; }
  html, body {
    width: 1200px; height: 780px; overflow: hidden;
    background: var(--backdrop);
  }
  .canvas {
    width: 1200px; height: 780px;
    display: flex; align-items: center; justify-content: center; gap: 40px;
    font-family: "Michroma", sans-serif;
  }
  .card {
    width: 540px; height: 310px;
    background: var(--card);
    border: 1px solid var(--card-edge);
    border-radius: 10px;
    position: relative;
    box-shadow: 0 18px 40px rgba(0,0,0,.45);
  }
  .card-front { display: flex; align-items: center; justify-content: center; }
  .wordmark { display: flex; align-items: center; gap: 14px; }
  .wordmark-dot {
    width: 22px; height: 22px; border-radius: 50%;
    background: var(--blue); flex: none;
  }
  .wordmark-name {
    color: var(--green);
    font-size: 19px; line-height: 1.5;
    letter-spacing: 1px; text-transform: uppercase;
  }
  .card-back { display: flex; align-items: center; }
  .card-back .brand-side {
    width: 270px; height: 100%;
    display: flex; align-items: center; justify-content: center;
  }
  .card-back .wordmark-name { font-size: 15px; }
  .card-back .wordmark { gap: 10px; }
  .card-back .wordmark-dot { width: 16px; height: 16px; }
  .divider { width: 1px; height: 190px; background: var(--divider); flex: none; }
  .details { padding-left: 26px; color: var(--white); text-transform: uppercase; }
  .person-name { color: var(--blue); font-size: 15px; letter-spacing: 2px; }
  .person-role { font-size: 9px; letter-spacing: 1.5px; margin-top: 2px; }
  .address { font-size: 10px; letter-spacing: 1.5px; line-height: 1.7; margin-top: 26px; }
  .contact-list { list-style: none; margin-top: 10px; }
  .contact-item {
    display: flex; align-items: center; gap: 8px;
    font-size: 10px; letter-spacing: 1.5px; line-height: 1.9;
  }
  .contact-email { text-transform: none; }
  .contact-icon {
    width: 14px; height: 14px; background: var(--green);
    border-radius: 2px; display: flex; align-items: center; justify-content: center; flex: none;
  }
  .contact-icon svg { width: 10px; height: 10px; }
</style>
</head>
<body>
<main class="canvas">
  <section class="card card-front" aria-label="Card front">
    <div class="wordmark">
      <span class="wordmark-dot"></span>
      <span class="wordmark-name">Flowbend<br>Industries</span>
    </div>
  </section>

  <section class="card card-back" aria-label="Card back">
    <div class="brand-side">
      <div class="wordmark">
        <span class="wordmark-dot"></span>
        <span class="wordmark-name">Flowbend<br>Industries</span>
      </div>
    </div>
    <div class="divider"></div>
    <div class="details">
      <p class="person-name">Glen Marsh</p>
      <p class="person-role">Director</p>
      <p class="address">17 Dorwell St<br>Tarrowell NSW 2794</p>
      <ul class="contact-list">
        <li class="contact-item">
          <span class="contact-icon">
            <svg viewBox="0 0 10 10"><path d="M2 1h2l1 2-1 1a5 5 0 0 0 2 2l1-1 2 1v2c-4 1-9-4-7-7z" fill="var(--icon-ink)"/></svg>
          </span>
          0438 760 514
        </li>
        <li class="contact-item contact-email">
          <span class="contact-icon">
            <svg viewBox="0 0 10 10"><rect x="1" y="2.5" width="8" height="5" fill="none" stroke="var(--icon-ink)" stroke-width="1"/><path d="M1 2.5l4 3 4-3" fill="none" stroke="var(--icon-ink)" stroke-width="1"/></svg>
          </span>
          Sales@flowbend.com.au
        </li>
      </ul>
    </div>
  </section>
</main>
</body>
</html>
```